Business card design for a dynamic IT consulting company

We need a business card design for a young firm, specialized in the Telecommunications/Consulting industry. The name of the company is Quindor and Partners Business Consulting Ltd. (Short name: Quindor and Partnes)
Quindor = solve read reverse, so we aim to be uncomplicated and solution-oriented. The small pipe in our logo is also related to the word solve. So we need a new business card design, which is simple, eye catching and something non traditional (I would probably prefer a square shaped design rather than a rectangle, but open for suggestions). Attached our logo.

Target Market(s)

Usually our customers are Tier1 Telecoms providers (Q-Netra, Palorix, etc) and their executives.

Industry/Entity Type

Business

Contact Information for Business Card

Name: Bence Tolnavari
Email: b.tolnavari@quindor.hu
Web: www.quindor.hu
Mobile: +36 30 518 2769
Title: Managing Director

Optional:
Company name: Quindor and Partners Ltd.
Address: 1087 Budapest, Tolvenka str. 28/C, Hungary

Font styles to use
Other font styles liked:
• helveticaneue_medium, Prime Regular are used now.

Colors

Designer to choose colors to be used in the design.

Requirements
Must have
• I would like to have a 2 sided design.
Nice to have
• I thought if we make the logo a bit bigger (without the company name), that could go to the back with the company name below. I though, if the pipe in the logo is somehow touchable on the business card, would be nice and unique.

```html
<!DOCTYPE html>
<html lang="en">
<head>
<meta charset="utf-8">
<title>Quindor and Partners – Business Card</title>
<link rel="stylesheet" href="https://fonts.googleapis.com/css2?family=Exo+2:wght@500&family=Roboto:wght@400&display=swap">
<style>
  :root {
    --page-bg: #d8d3cb;
    --card-light: #f1f1f3;
    --card-mid: #e3e4e8;
    --ink-dark: #2b2b30;
    --band-magenta: #9a2f7d;
    --band-magenta-deep: #7b2064;
    --panel-dark: #2e2e31;
    --panel-darker: #1f1f22;
    --text-light: #e6e6e6;
    --text-soft: #cfcfd2;
    --text-rose: #c79bb8;
    --icon-blue: #1f6a94;
    --accent-blue: #1566b0;
  }
  html, body {
    margin: 0;
    width: 1200px;
    height: 970px;
    overflow: hidden;
    background: var(--page-bg);
  }
  .canvas {
    position: relative;
    width: 1200px;
    height: 970px;
  }
  .card {
    position: absolute;
    left: 79px;
    top: 188px;
    width: 1042px;
    height: 594px;
    background: linear-gradient(160deg, var(--card-light) 0%, var(--card-mid) 100%);
    box-shadow: 0 6px 24px rgba(0,0,0,0.18);
    overflow: hidden;
  }
  .brand {
    position: absolute;
    left: 56px;
    top: 112px;
    display: flex;
    align-items: center;
    gap: 22px;
  }
  .brand-square {
    width: 30px;
    height: 30px;
    background: var(--ink-dark);
  }
  .brand-name {
    font-family: "Roboto", sans-serif;
    font-weight: 400;
    font-size: 58px;
    line-height: 1;
    color: var(--ink-dark);
  }
  .name-band {
    position: absolute;
    left: 0;
    top: 303px;
    width: 629px;
    height: 56px;
    background: linear-gradient(180deg, var(--band-magenta) 0%, var(--band-magenta-deep) 100%);
    display: flex;
    align-items: center;
  }
  .person-name {
    margin-left: 56px;
    font-family: "Exo 2", sans-serif;
    font-weight: 500;
    font-size: 34px;
    color: var(--text-light);
    letter-spacing: 0.5px;
  }
  .band-divider {
    width: 2px;
    height: 42px;
    background: rgba(255,255,255,0.75);
    margin: 0 26px 0 30px;
  }
  .person-title {
    font-family: "Roboto", sans-serif;
    font-size: 23px;
    color: #f1e3ec;
  }
  .contact-panel {
    position: absolute;
    left: 0;
    top: 362px;
    width: 629px;
    height: 232px;
    background: linear-gradient(180deg, var(--panel-dark) 0%, var(--panel-darker) 100%);
    font-family: "Roboto", sans-serif;
    color: var(--text-soft);
  }
  .address {
    position: absolute;
    left: 52px;
    top: 20px;
    font-size: 23px;
    line-height: 33px;
  }
  .contact-list {
    position: absolute;
    left: 52px;
    top: 100px;
    margin: 0;
    padding: 0;
    list-style: none;
    font-size: 23px;
  }
  .contact-list li {
    display: flex;
    align-items: center;
    gap: 12px;
    height: 32px;
    margin-bottom: 2px;
  }
  .contact-list svg { width: 28px; height: 28px; }
  .contact-email { color: var(--text-rose); }
  .pattern-area {
    position: absolute;
    left: 640px;
    top: 303px;
    width: 402px;
    height: 291px;
    background: linear-gradient(135deg, #5a5a60 0%, #3f7396 35%, #8d4a7c 65%, #4c83bd 100%);
    opacity: 0.55;
  }
</style>
</head>
<body>
<div class="canvas">
  <div class="card">
    <div class="brand">
      <span class="brand-square"></span>
      <span class="brand-name">Quindor and Partners Ltd.</span>
    </div>

    <div class="name-band">
      <span class="person-name">Bence Tolnavari</span>
      <span class="band-divider"></span>
      <span class="person-title">Managing Director</span>
    </div>

    <div class="contact-panel">
      <div class="address">1087 Budapest<br>Tolvenka str. 28/C, Hungary</div>
      <ul class="contact-list">
        <li>
          <svg viewBox="0 0 28 28" aria-hidden="true"><circle cx="14" cy="14" r="12.5" fill="none" stroke="var(--icon-blue)" stroke-width="1.5"/><rect x="10" y="7" width="8" height="14" rx="1.5" fill="none" stroke="var(--icon-blue)" stroke-width="1.5"/></svg>
          <span>+36 30 518 2769</span>
        </li>
        <li>
          <svg viewBox="0 0 28 28" aria-hidden="true"><circle cx="14" cy="14" r="12.5" fill="none" stroke="var(--icon-blue)" stroke-width="1.5"/><rect x="8" y="9.5" width="12" height="9" fill="none" stroke="var(--icon-blue)" stroke-width="1.5"/><path d="M8 9.5 L14 15 L20 9.5" fill="none" stroke="var(--icon-blue)" stroke-width="1.5"/></svg>
          <span class="contact-email">b.tolnavari@quindor.hu</span>
        </li>
        <li>
          <svg viewBox="0 0 28 28" aria-hidden="true"><circle cx="14" cy="14" r="12.5" fill="none" stroke="var(--icon-blue)" stroke-width="1.5"/><circle cx="14" cy="14" r="6.5" fill="none" stroke="var(--icon-blue)" stroke-width="1.5"/><path d="M7.5 14 H20.5 M14 7.5 V20.5" stroke="var(--icon-blue)" stroke-width="1.2"/></svg>
          <span>www.quindor.hu</span>
        </li>
      </ul>
    </div>

    <div class="pattern-area" role="img" aria-label="Decorative grid of dark, blue and magenta tiles"></div>
  </div>
</div>
</body>
</html>
```